design a construction company business card

Design business card around our logo. Card must have all the typical info: name, title, address, phone, email, business name, etc. Somewhere on the card I would like to see our motto "Founded on trust... Driven by dedication." Consider adding a splash of bright orange to the card to complement the blues and silvers/grays in the logo. We are open to metallic inks, textures, etc. We would like to see options on both light and dark backgrounds. The font in the logo is Euro Technic Extended Regular.

```html
<!DOCTYPE html>
<html lang="en">
<head>
<meta charset="utf-8">
<title>Halden Contracting – Business Card</title>
<link rel="stylesheet" href="https://fonts.googleapis.com/css2?family=Michroma&family=Questrial&display=swap">
<style>
  :root {
    --stage: #6b6b6d;
    --stage-dark: #3a3a3c;
    --card: #262628;
    --card-edge: #2e2e30;
    --brand-blue: #1f73d6;
    --text-light: #d2d2d4;
    --text-muted: #9c9ca0;
    --front-mark: #111113;
  }
  * { margin: 0; padding: 0; box-sizing: border-box; }
  html, body { width: 1200px; height: 1000px; overflow: hidden; }
  body {
    background: radial-gradient(ellipse at 50% 30%, var(--stage) 0%, var(--stage-dark) 100%);
    position: relative;
    font-family: "Questrial", sans-serif;
  }
  .card {
    position: absolute;
    left: 250px;
    width: 700px;
    height: 400px;
    border-radius: 26px;
    background: linear-gradient(160deg, var(--card-edge) 0%, var(--card) 60%);
    box-shadow: 0 18px 40px rgba(0,0,0,.45);
  }
  .card-front { top: 60px; }
  .card-back { top: 540px; }

  /* Front */
  .front-brand {
    position: absolute;
    top: 140px; left: 0; right: 0;
    text-align: center;
    font-family: "Michroma", sans-serif;
    color: var(--front-mark);
  }
  .front-brand .brand-name { font-size: 64px; letter-spacing: 2px; line-height: 1; }
  .front-brand .brand-sub { font-size: 20px; letter-spacing: 3px; margin-top: 10px; }
  .motto {
    position: absolute;
    top: 300px; left: 0; right: 0;
    text-align: center;
    font-family: "Michroma", sans-serif;
    font-size: 14px;
    letter-spacing: 1px;
    color: var(--brand-blue);
  }

  /* Back */
  .person { position: absolute; left: 50px; top: 155px; }
  .person-name {
    font-family: "Michroma", sans-serif;
    font-size: 20px;
    color: var(--brand-blue);
  }
  .person-title { font-size: 15px; color: var(--text-muted); margin-top: 6px; }

  .back-brand {
    position: absolute;
    right: 60px; top: 90px;
    text-align: center;
    font-family: "Michroma", sans-serif;
    color: var(--brand-blue);
  }
  .back-brand .brand-name { font-size: 54px; letter-spacing: 2px; line-height: 1; }
  .back-brand .brand-sub { font-size: 17px; letter-spacing: 3px; margin-top: 8px; }

  .contact {
    position: absolute;
    right: 40px; top: 258px;
    text-align: right;
    color: var(--text-light);
    font-size: 16px;
    line-height: 23px;
    list-style: none;
  }
  .contact li { display: flex; justify-content: flex-end; align-items: center; gap: 10px; }
  .contact .icon { width: 13px; height: 13px; flex: none; }
  .contact .spacer { width: 13px; flex: none; }
  .contact .accent { color: var(--brand-blue); }
</style>
</head>
<body>

<section class="card card-front">
  <div class="front-brand">
    <div class="brand-name">HALDEN</div>
    <div class="brand-sub">CONTRACTING, INC.</div>
  </div>
  <p class="motto">FOUNDED ON TRUST... DRIVEN BY DEDICATION.</p>
</section>

<section class="card card-back">
  <div class="person">
    <div class="person-name">Marcus Reed</div>
    <div class="person-title">Managing Director</div>
  </div>

  <div class="back-brand">
    <div class="brand-name">HALDEN</div>
    <div class="brand-sub">CONTRACTING, INC.</div>
  </div>

  <ul class="contact">
    <li>4820 Harbor Avenue<span class="spacer"></span></li>
    <li>Eastfield NY 10230<span class="spacer"></span></li>
    <li>555.014.2200
      <svg class="icon" viewBox="0 0 16 16" aria-hidden="true"><circle cx="8" cy="8" r="8" fill="#1f73d6"/><path d="M5 4.5l1.6-.4 1 2-1 .8a5 5 0 0 0 2.5 2.5l.8-1 2 1-.4 1.6c-3.5 0-6.5-3-6.5-6.5z" fill="#fff"/></svg>
    </li>
    <li>marcus@haldenbuild.com
      <svg class="icon" viewBox="0 0 16 16" aria-hidden="true"><circle cx="8" cy="8" r="8" fill="#1f73d6"/><rect x="4" y="5" width="8" height="6" fill="none" stroke="#fff" stroke-width="1.2"/><path d="M4 5l4 3.5L12 5" fill="none" stroke="#fff" stroke-width="1.2"/></svg>
    </li>
    <li><span>www.<span class="accent">haldenbuild</span>.com</span>
      <svg class="icon" viewBox="0 0 16 16" aria-hidden="true"><circle cx="8" cy="8" r="8" fill="#1f73d6"/><circle cx="8" cy="8" r="4.5" fill="none" stroke="#fff" stroke-width="1"/><ellipse cx="8" cy="8" rx="2" ry="4.5" fill="none" stroke="#fff" stroke-width="1"/><path d="M3.5 8h9" stroke="#fff" stroke-width="1"/></svg>
    </li>
  </ul>
</section>

</body>
</html>
```